Business Card & Email Signature Design || Upmarket + Luxury

Rima Vale Honey, a New Zealand Manuka Honey company needs a Business Card & Email Signature design.

Our logo's are attached in Gold & Black versions, feel free to be creative with how you use the logo and it's patterns in your design.

Style:
- Looking for an Elegant, Luxurious, Upmarket feel.
- Black/Matte Black Card, Gold Foil, UV Embossing

Information to Add:

- Logo
- Company Name: Rima Vale Honey
- Name: Martin Holloway
- Title: Creative Director
- Phone: +64 2815 96 417
- Email: martin@rimavalehoney.example.nz
- Website: www.rimavalehoney.example.nz

- Socials: ***For email Signature Only***
- Facebook: https://www.facebook.com/rimavalehoney/
- Instagram: https://www.instagram.com/rimavalehoney/

Target Market(s)

Asia/Europe Luxury, Upmarket

Contact Information for Business Card

- Logo
- Name: Martin Holloway
- Phone: +64 2815 96 417

Font styles to use
Other font styles liked:
• Champagne & Limousines (Attached)

Requirements
Must have
• Business Card & Email Signature Design.

Looking for a Sleek, Luxury, Upmarket Design.

```html
<!DOCTYPE html>
<html lang="en">
<head>
<meta charset="utf-8">
<title>Rima Vale Honey – Business Card</title>
<link rel="stylesheet" href="https://fonts.googleapis.com/css2?family=Josefin+Sans:wght@300&family=Open+Sans:wght@400;700&display=swap">
<style>
  :root {
    --backdrop: #2b2b2b;
    --backdrop-deep: #1e1e1e;
    --card: #121212;
    --card-tone: #1b1b1b;
    --silver: #d9d9d9;
    --gold: #d9b24a;
    --gold-soft: #e6c971;
    --leaf-green: #8cb12a;
    --text-light: #e8e8e8;
  }
  * { box-sizing: border-box; margin: 0; padding: 0; }
  html, body { width: 1200px; height: 1017px; overflow: hidden; }
  body {
    background: radial-gradient(ellipse at 50% 30%, var(--backdrop) 0%, var(--backdrop-deep) 100%);
    font-family: "Open Sans", Arial, sans-serif;
    position: relative;
  }
  .card {
    position: absolute;
    left: 280px;
    width: 640px;
    height: 366px;
    background: var(--card);
    border-radius: 4px;
    box-shadow: 0 18px 40px rgba(0,0,0,0.55);
    overflow: hidden;
  }
  .card--front { top: 100px; }
  .card--back { top: 551px; }
  .card__texture {
    position: absolute; inset: 0;
    background:
      radial-gradient(circle at 25% 30%, var(--card-tone) 0%, transparent 45%),
      radial-gradient(circle at 75% 70%, var(--card-tone) 0%, transparent 45%),
      var(--card);
  }
  .brand-mark {
    position: absolute;
    display: flex; align-items: center; gap: 16px;
    font-family: "Josefin Sans", "Helvetica Neue", sans-serif;
    font-weight: 300;
    text-transform: uppercase;
    white-space: nowrap;
  }
  .brand-mark__dot {
    border-radius: 50%;
    border: 1.5px solid currentColor;
  }
  .card--front .brand-mark {
    left: 50%; top: 50%;
    transform: translate(-50%, -50%);
    color: var(--silver);
    font-size: 30px;
    letter-spacing: 0.32em;
  }
  .card--front .brand-mark__dot { width: 22px; height: 22px; }
  .card--back .brand-mark {
    right: 44px; top: 58px;
    color: var(--gold);
    font-size: 22px;
    letter-spacing: 0.24em;
  }
  .card--back .brand-mark__dot { width: 16px; height: 16px; }
  .contact {
    position: absolute;
    left: 48px; bottom: 44px;
  }
  .contact__name {
    color: var(--gold-soft);
    font-weight: 700;
    font-size: 23px;
    letter-spacing: 0.06em;
    text-transform: uppercase;
  }
  .contact__title {
    color: var(--leaf-green);
    font-size: 15px;
    margin: 2px 0 14px;
  }
  .contact__list { list-style: none; }
  .contact__item {
    display: flex; align-items: center; gap: 10px;
    color: var(--text-light);
    font-size: 13.5px;
    line-height: 22px;
  }
  .contact__icon { width: 12px; height: 12px; flex: none; }
</style>
</head>
<body>

<section class="card card--front" aria-label="Business card front">
  <div class="card__texture" role="img" aria-label="Embossed floral damask pattern on matte black card"></div>
  <div class="brand-mark">
    <span class="brand-mark__dot"></span>
    <span class="brand-mark__name">Rima Vale Honey</span>
  </div>
</section>

<section class="card card--back" aria-label="Business card back">
  <div class="card__texture" role="img" aria-label="Embossed floral damask pattern on matte black card"></div>
  <div class="brand-mark">
    <span class="brand-mark__dot"></span>
    <span class="brand-mark__name">Rima Vale Honey</span>
  </div>

  <div class="contact">
    <p class="contact__name">Martin Holloway</p>
    <p class="contact__title">Creative Director</p>
    <ul class="contact__list">
      <li class="contact__item">
        <svg class="contact__icon" viewBox="0 0 12 12" aria-hidden="true">
          <path d="M3 1 L5 3.5 L3.8 5 Q5 7.5 7 8.2 L8.5 7 L11 9 L9.5 11 Q3 10.5 1 2.5 Z" fill="var(--gold)"/>
        </svg>
        <span>+64 2815 96 417</span>
      </li>
      <li class="contact__item">
        <svg class="contact__icon" viewBox="0 0 12 12" aria-hidden="true">
          <rect x="0.5" y="2.5" width="11" height="7.5" fill="var(--gold)"/>
          <path d="M0.5 2.5 L6 7 L11.5 2.5" fill="none" stroke="var(--card)" stroke-width="1"/>
        </svg>
        <span>martin@rimavalehoney.example.nz</span>
      </li>
      <li class="contact__item">
        <svg class="contact__icon" viewBox="0 0 12 12" aria-hidden="true">
          <circle cx="6" cy="6" r="5.5" fill="var(--gold)"/>
          <path d="M0.5 6 H11.5 M6 0.5 Q2.5 6 6 11.5 M6 0.5 Q9.5 6 6 11.5" fill="none" stroke="var(--card)" stroke-width="0.9"/>
        </svg>
        <span>www.rimavalehoney.example.nz</span>
      </li>
    </ul>
  </div>
</section>

</body>
</html>
```